Im open to ideas.. I was thinking on my business cards aswell as my logo. a place for my name. email. phone number and abn..

ive attched a file with my business logo. which i dont love the colours.. i was think a dark background with charcoal letters so something along those colour schumes but im open to ideas..

BRM Constructions

```html
<!DOCTYPE html>
<html lang="en">
<head>
<meta charset="utf-8">
<title>BRM Constructions – Business Card</title>
<link rel="stylesheet" href="https://fonts.googleapis.com/css2?family=Arimo:wght@400;700&display=swap">
<style>
  :root {
    --page-bg: #e9e6e1;
    --card-white: #ffffff;
    --charcoal: #1f1f1f;
    --band-black: #111111;
    --band-text: #f2f2f2;
    --band-muted: #bdbdbd;
    --brand-red: #d40f14;
    --brand-red-deep: #8f0b0e;
    --web-pink: #f4c9ca;
    --card-shadow: 0 12px 30px rgba(0, 0, 0, 0.25);
  }
  * { box-sizing: border-box; margin: 0; padding: 0; }
  html, body {
    width: 1200px;
    height: 950px;
    overflow: hidden;
    background: var(--page-bg);
    font-family: "Arimo", Arial, sans-serif;
  }
  .sheet {
    width: 1200px;
    height: 950px;
    display: flex;
    flex-direction: column;
    align-items: center;
    justify-content: center;
    gap: 50px;
  }
  .card {
    position: relative;
    width: 680px;
    height: 416px;
    border-radius: 4px;
    box-shadow: var(--card-shadow);
    overflow: hidden;
  }

  /* Back of card */
  .card--back {
    background: linear-gradient(110deg, var(--brand-red) 0%, #c00d12 55%, var(--brand-red-deep) 100%);
    display: flex;
    flex-direction: column;
    align-items: center;
    justify-content: center;
    gap: 22px;
  }
  .card--back .wordmark { color: var(--card-white); }
  .card--back .wordmark__mark { background: var(--card-white); }
  .web-address {
    color: var(--web-pink);
    font-size: 17px;
    letter-spacing: 2px;
  }

  /* Brand name */
  .wordmark {
    display: flex;
    align-items: center;
    gap: 14px;
    color: var(--charcoal);
    font-weight: 700;
    font-size: 44px;
    letter-spacing: 1px;
  }
  .wordmark__mark {
    width: 26px;
    height: 26px;
    background: var(--brand-red);
  }

  /* Front of card */
  .card--front { background: var(--card-white); }
  .card--front .wordmark {
    position: absolute;
    top: 108px;
    left: 0;
    right: 0;
    justify-content: center;
  }
  .contact-band {
    position: absolute;
    left: 0;
    right: 0;
    top: 262px;
    height: 118px;
    background: var(--band-black);
    display: flex;
    flex-direction: column;
    justify-content: center;
    padding: 0 36px;
    gap: 14px;
  }
  .contact-band__name {
    text-align: center;
    color: var(--band-text);
    font-size: 22px;
    font-weight: 700;
  }
  .contact-band__role {
    font-weight: 400;
    color: var(--band-muted);
    font-size: 18px;
  }
  .contact-band__details {
    display: flex;
    justify-content: center;
    gap: 12px;
    white-space: nowrap;
    color: var(--band-muted);
    font-size: 15px;
    letter-spacing: 0.5px;
  }
</style>
</head>
<body>
  <main class="sheet">
    <section class="card card--back" aria-label="Card back">
      <div class="wordmark"><span class="wordmark__mark"></span>BRM Constructions</div>
      <p class="web-address">www.brmbuild.com</p>
    </section>

    <section class="card card--front" aria-label="Card front">
      <div class="wordmark"><span class="wordmark__mark"></span>BRM Constructions</div>
      <div class="contact-band">
        <p class="contact-band__name">Daniel Harlow - <span class="contact-band__role">President</span></p>
        <p class="contact-band__details">
          <span>ABN: 987654321</span><span>|</span>
          <span>P : 555 0142 7788</span><span>|</span>
          <span>E : daniel@brmbuild.com</span>
        </p>
      </div>
    </section>
  </main>
</body>
</html>
```